EMBER -- book design (5 x 8) boy 14 caught up in the 1838 Lower Canadian rebellion against the Brits

Boy must sell the book. So attractive while historic. Below is a well known picture drawn at the time of what the rebels looked like. My boy would probably have more in common with the guy in white than the others -- he was a lawyer's son.
TITLE: EMBER
AUTHOR: ROSALIND TREMAINE

```html
<!DOCTYPE html>
<html lang="en">
<head>
<meta charset="utf-8">
<title>Ember — Book Cover Wrap</title>
<link href="https://fonts.googleapis.com/css2?family=Playfair+Display:ital,wght@0,400;0,700;1,400&display=swap" rel="stylesheet">
<style>
  :root {
    --navy: #0c2238;
    --red: #c0201f;
    --frame-red: #b3262a;
    --white: #f4f4f4;
    --scene-night: #0a0b0e;
    --scene-smoke: #3c3e44;
    --scene-coat: #9ea3ab;
    --scene-steel: #2c4763;
    --scene-ember: #5a1c14;
  }
  * { margin: 0; padding: 0; box-sizing: border-box; }
  html, body { width: 1200px; height: 831px; overflow: hidden; background: var(--navy); }
  .cover {
    position: relative; width: 1200px; height: 831px;
    font-family: "Playfair Display", Georgia, serif; color: var(--white);
  }
  .back-panel { position: absolute; left: 0; top: 0; width: 646px; height: 831px; background: var(--navy); }
  .front-scene {
    position: absolute; left: 646px; top: 0; width: 554px; height: 831px;
    background:
      radial-gradient(ellipse 20% 42% at 50% 58%, var(--scene-coat) 0%, rgba(158,163,171,0.35) 40%, transparent 72%),
      radial-gradient(ellipse 22% 40% at 18% 70%, var(--scene-steel) 0%, transparent 70%),
      radial-gradient(ellipse 22% 45% at 85% 62%, var(--scene-smoke) 0%, transparent 70%),
      radial-gradient(ellipse 70% 30% at 50% 100%, var(--scene-ember) 0%, transparent 75%),
      linear-gradient(170deg, var(--scene-night) 0%, #17181c 50%, #26272c 100%);
  }
  .frames { position: absolute; inset: 0; }

  .author-photo {
    position: absolute; left: 70px; top: 69px; width: 110px; height: 139px;
    background: linear-gradient(180deg, #9a7a5a 0%, #6c5340 55%, #1d1d22 100%);
  }
  .bio-name { position: absolute; left: 196px; top: 184px; font-size: 21px; font-weight: 400; }
  .bio {
    position: absolute; left: 69px; top: 224px; width: 416px;
    font-style: italic; font-size: 12.1px; line-height: 17.1px; text-align: justify;
  }
  .books-heading { position: absolute; left: 69px; top: 429px; font-size: 12.4px; }
  .books-list {
    position: absolute; left: 69px; top: 463px; list-style: none;
    font-style: italic; font-size: 12.4px; line-height: 17.1px;
  }
  .publisher {
    position: absolute; left: 146px; top: 774px; width: 250px; text-align: center;
    font-size: 15px; letter-spacing: 0.3px;
  }

  .spine-title, .spine-author {
    position: absolute; writing-mode: vertical-rl; left: 600px; transform: translateX(-50%);
  }
  .spine-title { top: 44px; font-size: 40px; font-weight: 700; color: var(--red); line-height: 1; }
  .spine-author { top: 544px; font-size: 28px; color: var(--white); line-height: 1; }

  .front-title {
    position: absolute; left: 692px; width: 462px; top: 364px; text-align: center;
    font-size: 88px; font-weight: 700; color: var(--red); line-height: 1;
  }
  .front-author {
    position: absolute; left: 692px; width: 462px; top: 766px; text-align: center;
    font-size: 31px; color: var(--white); line-height: 1;
  }
</style>
</head>
<body>
<main class="cover">
  <section class="back-panel" aria-label="Back cover and spine"></section>
  <div class="front-scene" role="img" aria-label="Night scene from the 1838 Lower Canadian rebellion: a 14-year-old boy, a lawyer's son in a pale coat, stands among armed rebels in dark winter coats and tuques, lit by smoke and the glow of embers"></div>

  <svg class="frames" width="1200" height="831" viewBox="0 0 1200 831" aria-hidden="true">
    <g fill="none" stroke="var(--frame-red)" stroke-width="1">
      <polyline points="138,784.5 46.5,784.5 46.5,46.5 507.5,46.5 507.5,784.5 415,784.5"/>
      <line x1="600" y1="206" x2="600" y2="499"/>
      <polyline points="800,784.5 692.5,784.5 692.5,46.5 1154.5,46.5 1154.5,784.5 1044,784.5"/>
    </g>
  </svg>

  <div class="author-photo" role="img" aria-label="Portrait photo of the author"></div>
  <h2 class="bio-name">Rosalind Tremaine</h2>
  <p class="bio">When Roz was 15, she fell in love – with words. One Friday night, she raced into a store, looking for the latest Margery Hale murder mystery and bought instead T.R. Ashby's Murder in a Chapel. Hours later, she realized it was poetic drama. Unable to take the book back, and unwilling to waste her money, she started reading and suddenly understood the majesty of words. Since then Roz has known the publishing world as a teacher, scholar, and publisher. She's the writer of 18 books ranging from academic history to young adult fiction. More recently, she's been sharing her knowledge — teaching at conferences, in schools, wherever. She is the Director of Write Harbourside (a writers' conference) and the Regional Director of The Quill Society, a national writers' organization.</p>
  <p class="books-heading">BOOKS:</p>
  <ul class="books-list">
    <li>Marie's Rebellion</li>
    <li>Anchored in Hope</li>
    <li>Marie's Treason</li>
    <li>Eight People Meet Grace</li>
    <li>Eight Surprises and Stories of Faith</li>
    <li>Quiet Joy: Quiet Worthy</li>
  </ul>
  <p class="publisher">ASHGROVE COVE BOOKS</p>

  <p class="spine-title">Ember</p>
  <p class="spine-author">Rosalind Tremaine</p>

  <h1 class="front-title">Ember</h1>
  <p class="front-author">Rosalind Tremaine</p>
</main>
</body>
</html>
```